4747 5858

Web(re)design of an existing directory search site www.le5858.be (in Dutch www.de4747.be and in English www.3838.be).

This site is a directory site, i.e. a "white pages" site whereby people can search the phone & details of another person based on a combination of name + city (for instance smith in Brussels); one can also search a company also based on a combination of name + city (for instance Vornak in Brussels); last but not least one can also search the name of the subscriber behind a specific telephone number (also called reverse search).

This site is quite outdated and needs a redesign, see instructions.

We need the output in XD format.

```html
<!DOCTYPE html>
<html lang="fr">
<head>
<meta charset="utf-8">
<title>Les Renseignements CINQ-HUIT Utiles</title>
<link href="https://fonts.googleapis.com/css2?family=Roboto+Condensed:wght@300;400;700&family=Roboto:wght@400&display=swap" rel="stylesheet">
<style>
:root{
  --red:#d61f26;
  --red-dark:#b8141b;
  --ink:#333333;
  --muted:#555555;
  --band:#f2f2f2;
  --line:#cfcfcf;
  --white:#ffffff;
}
*{box-sizing:border-box;margin:0;padding:0}
html,body{width:1200px;height:600px;overflow:hidden;background:var(--white)}
body{font-family:"Roboto Condensed",Arial,sans-serif;color:var(--ink);position:relative}
.site-header{position:absolute;left:0;top:0;width:1200px;height:128px;background:var(--band)}
.header-corner{position:absolute;left:0;top:0;width:300px;height:260px}
.brand{position:absolute;left:30px;top:38px;display:flex;align-items:center;gap:7px;
  font-size:34px;font-weight:700;color:var(--red);letter-spacing:-0.5px}
.brand-dot{width:14px;height:14px;border-radius:50%;background:var(--red)}
.site-title{position:absolute;left:0;width:1200px;top:40px;text-align:center;
  font-size:35px;font-weight:400;color:var(--ink)}
.site-title em{font-style:normal;color:var(--red)}
.lang{position:absolute;left:1097px;top:53px;font-size:17px;color:var(--muted)}
.lang svg{vertical-align:middle;margin-left:2px}
.menu{position:absolute;left:1155px;top:57px;width:23px}
.menu span{display:block;height:2px;background:var(--ink);margin-bottom:5px}
.tabs{position:absolute;top:156px;left:0;width:1200px;display:flex;justify-content:center;
  font-size:19px;list-style:none}
.tabs li{padding:0 23px;border-left:1px solid var(--line);line-height:20px}
.tabs li:first-child{border-left:none}
.tabs li.active{color:var(--red)}
.search-form{position:absolute;left:173px;top:224px;width:855px;display:flex;justify-content:space-between}
.field{width:263px;text-align:center}
.field label{display:block;font-size:17px;font-weight:700;margin-bottom:12px}
.field .input{height:42px;border:1px solid var(--line);border-radius:21px;background:var(--white)}
.field .hint{margin-top:8px;font-size:12px;font-weight:300;color:var(--muted)}
.captcha{position:absolute;left:488px;top:347px;width:224px;height:54px;background:#f9f9f9;
  border:1px solid #e5e5e5;font-family:Roboto,Arial,sans-serif}
.captcha .box{position:absolute;left:9px;top:15px;width:20px;height:20px;border:2px solid #c1c1c1;border-radius:2px;background:var(--white)}
.captcha .label{position:absolute;left:38px;top:20px;font-size:10px;color:#222}
.captcha .mark{position:absolute;left:181px;top:9px;width:20px;height:20px;border-radius:4px;background:#8fa7d8}
.captcha .name{position:absolute;right:8px;top:33px;font-size:7px;color:#555}
.captcha .terms{position:absolute;right:8px;top:43px;font-size:5.5px;color:#555}
.submit{position:absolute;left:540px;top:427px;width:120px;height:42px;border-radius:21px;
  background:linear-gradient(#dd2229,var(--red-dark));color:var(--white);font-size:19px;font-weight:700;
  display:flex;align-items:center;justify-content:center}
.ghost-brand{position:absolute;left:1010px;top:338px;width:160px;height:150px}
.site-footer{position:absolute;left:0;top:514px;width:1200px;height:86px;background:var(--band)}
.footer-links{position:absolute;left:171px;top:22px;list-style:none;display:flex;font-size:14px;color:var(--muted)}
.footer-links li{padding:0 10px;border-left:1px solid var(--line);line-height:14px}
.footer-links li:first-child{padding-left:0;border-left:none}
.copyright{position:absolute;left:171px;top:44px;font-size:14px;color:var(--muted)}
.partner-badge{position:absolute;left:938px;top:18px;width:70px;height:50px}
</style>
</head>
<body>
<header class="site-header">
  <svg class="header-corner" viewBox="0 0 300 260" aria-hidden="true">
    <polygon points="0,0 281,0 0,248" fill="#ffffff"/>
  </svg>
  <div class="brand"><span class="brand-dot"></span>58·58</div>
  <h1 class="site-title">Les Renseignements <em>CINQ-HUIT</em> Utiles</h1>
  <div class="lang">FR<svg width="8" height="6" viewBox="0 0 8 6"><path d="M1 1l3 3 3-3" fill="none" stroke="#555" stroke-width="1"/></svg></div>
  <div class="menu"><span></span><span></span><span></span></div>
</header>

<ul class="tabs">
  <li class="active">Particuliers</li>
  <li>Sociétés</li>
  <li>Annuaire inversé</li>
  <li>International</li>
</ul>

<div class="search-form">
  <div class="field"><label>Nom de famille:</label><div class="input"></div><div class="hint">Ex: Dupont, Janssens, ...</div></div>
  <div class="field"><label>Prénom:</label><div class="input"></div><div class="hint">Ex: Jan, Louis, ...</div></div>
  <div class="field"><label>Localité:</label><div class="input"></div><div class="hint">Ex: Liége, Anvers, 1150, ....</div></div>
</div>

<div class="captcha">
  <div class="box"></div>
  <div class="label">I'm not a robot</div>
  <div class="mark"></div>
  <div class="name">VeriCheck</div>
  <div class="terms">Privacy - Terms</div>
</div>

<div class="submit">58-58!</div>

<svg class="ghost-brand" viewBox="0 0 160 150" aria-hidden="true">
  <circle cx="18" cy="70" r="10" fill="#f3f3f3"/>
  <text x="36" y="88" font-family="Roboto Condensed, sans-serif" font-weight="700" font-size="52" fill="#f3f3f3">58·58</text>
</svg>

<footer class="site-footer">
  <ul class="footer-links">
    <li>B2B Services</li>
    <li>Aide</li>
    <li>Conditions générales d'utilisation</li>
    <li>Respect de la vie privée</li>
  </ul>
  <p class="copyright">Copyright Norvia 2022, tous droits réservés.</p>
  <svg class="partner-badge" viewBox="0 0 70 50" aria-hidden="true">
    <rect x="8" y="6" width="54" height="38" rx="6" fill="#e2e2e2"/>
  </svg>
</footer>
</body>
</html>
```